Bicycle Tour Schedule on a Business Card

Need to develop a 2 side business card that highlights a series of bike tours on 1 side and a series of events on the other side.
This will be inserted into a card wallet that attaches to a cell phone and will be handed out at an expo. The card wallets are black and red so color must coordinate with both. There is a photo of the card wallets attached.

1 side needs to be devoted to Pedal Vista Trek and the others to KQR Venture events on the other. Dates and websites are very important.

Target Market(s)

Cyclists
Predominantly men ages 40+
Educated, Professionals

Industry/Entity Type

Business

Font styles to use
Serif

Requirements
Must have
• Pedal vista treks logo on 1 side and KQR Venture logo on the other side
• dates and websites clearly visible
• Design of both sides must go together.
• Must be portrait not landscape

```html
<!DOCTYPE html>
<html lang="en">
<head>
<meta charset="utf-8">
<title>Pedal Vista Treks and KQR Venture – Event Cards</title>
<link rel="stylesheet" href="https://fonts.googleapis.com/css2?family=Source+Sans+3:ital,wght@0,400;0,600;0,700;1,700&display=swap">
<style>
  :root {
    --backdrop: #e4e4e4;
    --card: #f5f5f4;
    --ink: #3d3d3d;
    --ink-strong: #2e2e2e;
    --tour-blue: #1456a8;
    --tour-green: #3aa447;
    --event-red: #c8102e;
    --event-teal: #1f8db0;
  }
  * { box-sizing: border-box; margin: 0; padding: 0; }
  html, body {
    width: 1105px;
    height: 1200px;
    overflow: hidden;
    background: var(--backdrop);
    font-family: "Source Sans 3", sans-serif;
    color: var(--ink);
  }
  .card {
    position: absolute;
    top: 251px;
    width: 398px;
    height: 697px;
    background: var(--card);
  }
  .card--tours { left: 111px; }
  .card--events { left: 596px; }

  .brand {
    position: absolute;
    display: flex;
    align-items: center;
    gap: 12px;
  }
  .brand__name {
    font-weight: 700;
    font-size: 34px;
    line-height: 1;
  }
  .brand__mark { flex: none; }
  .card--tours .brand { left: 43px; top: 110px; }
  .card--tours .brand__name { color: var(--tour-blue); }
  .card--events .brand { left: 43px; top: 110px; }
  .card--events .brand__name { color: var(--event-red); }

  .tagline {
    position: absolute;
    left: 43px;
    right: 30px;
    font-weight: 700;
    font-style: italic;
    font-size: 20.5px;
    line-height: 1.2;
  }
  .tagline::before {
    content: "";
    position: absolute;
    left: -43px;
    top: 0;
    bottom: 0;
    width: 8px;
  }
  .card--tours .tagline { top: 269px; color: var(--tour-blue); }
  .card--tours .tagline::before { background: var(--tour-blue); }
  .card--events .tagline { top: 244px; color: var(--event-red); }
  .card--events .tagline::before { background: var(--event-red); }

  .schedule {
    position: absolute;
    left: 43px;
    right: 20px;
    list-style: none;
  }
  .card--tours .schedule { top: 374px; }
  .card--events .schedule { top: 313px; }
  .schedule__item { font-size: 18.5px; line-height: 1.22; }
  .card--tours .schedule__item + .schedule__item { margin-top: 18px; }
  .card--events .schedule__item + .schedule__item { margin-top: 14px; }
  .card--events .schedule__item--gap { margin-top: 24px !important; }
  .schedule__name { display: block; font-weight: 400; color: var(--ink); }
  .schedule__date,
  .schedule__site { display: block; font-weight: 600; color: var(--ink-strong); }
</style>
</head>
<body>

<section class="card card--tours" aria-label="Pedal Vista Treks tour schedule">
  <div class="brand">
    <svg class="brand__mark" width="22" height="22" viewBox="0 0 22 22" aria-hidden="true">
      <circle cx="11" cy="11" r="11" fill="var(--tour-green)"/>
    </svg>
    <span class="brand__name">Pedal Vista Treks</span>
  </div>

  <p class="tagline">Fully supported bike tours.<br>Discover the hidden gems on<br>two wheels</p>

  <ul class="schedule">
    <li class="schedule__item">
      <span class="schedule__name">Heart of Colorado</span>
      <span class="schedule__date">June 26 - July 2, 2016</span>
    </li>
    <li class="schedule__item">
      <span class="schedule__name">Colorado Front Range Tour</span>
      <span class="schedule__date">August 14-20, 2016</span>
    </li>
    <li class="schedule__item">
      <span class="schedule__name">Cape Cod Tour</span>
      <span class="schedule__date">October 9 -15, 2016</span>
    </li>
    <li class="schedule__item">
      <span class="schedule__name">Florida Key Tours</span>
      <span class="schedule__date">November 6-12, 2016 &amp;</span>
      <span class="schedule__date">December 4-10, 2016</span>
    </li>
  </ul>
</section>

<section class="card card--events" aria-label="KQR Venture event schedule">
  <div class="brand">
    <svg class="brand__mark" width="22" height="22" viewBox="0 0 22 22" aria-hidden="true">
      <rect width="22" height="22" fill="var(--event-teal)"/>
    </svg>
    <span class="brand__name">KQR Venture</span>
  </div>

  <p class="tagline">Tri Spoke Series:<br>Cycling camps for youth</p>

  <ul class="schedule">
    <li class="schedule__item">
      <span class="schedule__name">Mountain Bike Camp</span>
      <span class="schedule__date">July 8-10, 2016</span>
    </li>
    <li class="schedule__item">
      <span class="schedule__name">Cyclocross Camp</span>
      <span class="schedule__date">August 26-28, 2016</span>
      <span class="schedule__site">Trispokeseries.org</span>
    </li>
    <li class="schedule__item schedule__item--gap">
      <span class="schedule__name">Summit Century Ride</span>
      <span class="schedule__date">June 18, 2016</span>
      <span class="schedule__site">Summitcenturyride.com</span>
    </li>
    <li class="schedule__item">
      <span class="schedule__name">Ridge 2 Ridge Challenge</span>
      <span class="schedule__date">July 30, 2016 - Ridge2ridge.com</span>
    </li>
    <li class="schedule__item">
      <span class="schedule__name">Zany Wheel Ride</span>
      <span class="schedule__date">September 11, 2016</span>
      <span class="schedule__site">zanywheelride.com</span>
    </li>
  </ul>
</section>

</body>
</html>
```